stationary deign for trucking company

im a trucking company looking for a professional set of stationary designs i deliver goods from point a to b
Updates

When submitting stationary designs I need envelope design, letterhead, cards, I’d badge etc

Industry/Entity Type

Trucking Company

Requirements
Must have
• must have letter head, business card, envelope, fax sheet, id badge, folder, thank you card, notebook, invoice sheet.
Nice to have
• nice to have them all custom made (letterhead,envelope, business card, I’d badge etc
Should not have
• must not have prepaid sign want i unique design for items

```html
<!DOCTYPE html>
<html lang="en">
<head>
<meta charset="utf-8">
<title>Kestrel Freight – Business Card</title>
<link href="https://fonts.googleapis.com/css2?family=Roboto:wght@400;500&display=swap" rel="stylesheet">
<style>
  :root {
    --page-bg: #e7e7e7;
    --card-bg: #1c1d1f;
    --accent-blue: #1565c0;
    --text-white: #ffffff;
    --divider: #d9d9d9;
    --brand-silver: #cfcfcf;
  }
  html, body {
    margin: 0;
    padding: 0;
    width: 1125px;
    height: 1200px;
    overflow: hidden;
    background: var(--page-bg);
    font-family: "Roboto", Arial, sans-serif;
  }
  .canvas {
    position: relative;
    width: 1125px;
    height: 1200px;
  }
  .card {
    position: absolute;
    left: 156px;
    width: 825px;
    height: 471px;
    background: var(--card-bg);
    box-shadow: 0 6px 18px rgba(0,0,0,0.25);
  }
  .card--front { top: 106px; }
  .card--back { top: 639px; }

  .identity {
    position: absolute;
    right: 465px;
    top: 200px;
    text-align: right;
  }
  .identity__name {
    margin: 0;
    font-size: 31px;
    font-weight: 500;
    color: var(--accent-blue);
    line-height: 1.1;
  }
  .identity__title {
    margin: 4px 0 0;
    font-size: 20px;
    font-weight: 500;
    color: var(--text-white);
    line-height: 1.1;
  }
  .divider {
    position: absolute;
    left: 388px;
    top: 170px;
    width: 2px;
    height: 129px;
    background: var(--divider);
  }
  .contact-list {
    position: absolute;
    left: 424px;
    top: 170px;
    margin: 0;
    padding: 0;
    list-style: none;
  }
  .contact-list__item {
    display: flex;
    align-items: center;
    height: 26.3px;
    font-size: 20px;
    color: var(--text-white);
  }
  .contact-list__icon {
    width: 18px;
    height: 18px;
    margin-right: 12px;
    fill: var(--accent-blue);
    flex: none;
  }
  .address {
    position: absolute;
    left: 0;
    right: 0;
    top: 393px;
    margin: 0;
    text-align: center;
    font-size: 20px;
    color: var(--text-white);
  }

  .brand {
    position: absolute;
    left: 0;
    right: 0;
    top: 210px;
    display: flex;
    justify-content: center;
    align-items: center;
    gap: 22px;
  }
  .brand__mark {
    width: 40px;
    height: 40px;
    border: 3px solid var(--brand-silver);
    box-sizing: border-box;
  }
  .brand__name {
    margin: 0;
    font-size: 46px;
    font-weight: 500;
    letter-spacing: 6px;
    color: var(--brand-silver);
    line-height: 1;
  }
</style>
</head>
<body>
<main class="canvas">
  <section class="card card--front" aria-label="Business card front">
    <div class="identity">
      <h1 class="identity__name">MARCUS HALE</h1>
      <p class="identity__title">CEO/FOUNDER</p>
    </div>
    <div class="divider"></div>
    <ul class="contact-list">
      <li class="contact-list__item">
        <svg class="contact-list__icon" viewBox="0 0 24 24" aria-hidden="true"><path d="M6.6 10.8a15.2 15.2 0 0 0 6.6 6.6l2.2-2.2c.3-.3.7-.4 1-.2 1.1.4 2.3.6 3.6.6.6 0 1 .4 1 1V20c0 .6-.4 1-1 1A17 17 0 0 1 3 4c0-.6.4-1 1-1h3.5c.6 0 1 .4 1 1 0 1.3.2 2.5.6 3.6.1.3 0 .7-.2 1z"/></svg>
        555 210 4471
      </li>
      <li class="contact-list__item">
        <svg class="contact-list__icon" viewBox="0 0 24 24" aria-hidden="true"><path d="M7 1h10a2 2 0 0 1 2 2v18a2 2 0 0 1-2 2H7a2 2 0 0 1-2-2V3a2 2 0 0 1 2-2zm0 3v14h10V4zm5 15.5a1 1 0 1 0 0 2 1 1 0 0 0 0-2z"/></svg>
        555 382 6690
      </li>
      <li class="contact-list__item">
        <svg class="contact-list__icon" viewBox="0 0 24 24" aria-hidden="true"><path d="M7 2h10v5H7zM4 8h16a2 2 0 0 1 2 2v7h-4v5H6v-5H2v-7a2 2 0 0 1 2-2zm4 8v4h8v-4z"/></svg>
        555 947 1205
      </li>
      <li class="contact-list__item">
        <svg class="contact-list__icon" viewBox="0 0 24 24" aria-hidden="true"><path d="M2 5h20v14H2zm2 2v.5l8 5 8-5V7l-8 5z"/></svg>
        marcus@kestrelfreight.com
      </li>
      <li class="contact-list__item">
        <svg class="contact-list__icon" viewBox="0 0 24 24" aria-hidden="true"><path d="M12 2a10 10 0 1 0 0 20 10 10 0 0 0 0-20zm-1 17.9A8 8 0 0 1 4.2 10.2L9 15v1a2 2 0 0 0 2 2zm6.9-2.5A2 2 0 0 0 16 16h-1v-3a1 1 0 0 0-1-1H8v-2h2a1 1 0 0 0 1-1V7h2a2 2 0 0 0 2-2v-.4a8 8 0 0 1 2.9 12.8z"/></svg>
        www.kestrelfreight.com
      </li>
    </ul>
    <p class="address">4120 Birchwood Road, Anchorage, Alaska 99507</p>
  </section>

  <section class="card card--back" aria-label="Business card back">
    <div class="brand">
      <span class="brand__mark" aria-hidden="true"></span>
      <p class="brand__name">KESTREL FREIGHT</p>
    </div>
  </section>
</main>
</body>
</html>
```